Box Design for Flooring product

***IMPORTANT: PLEASE READ THE DOCUMENT PROVIDED WITH THIS BRIEF CAREFULLY BEFORE ACCEPTING THIS PROJECT***
Need a creative design for the packaging of a flooring product. The packaging is two boxes: one holding 36 planks of flooring, and the other 7 planks of flooring. There are 4 colours for the flooring planks that need a box designed (for both the 36 plank box and 7 plank box). The boxes measures 92 cm x 16cm x 7cm (36 planks) and 92 cm x 16cm x 1.5cm (7 planks).
More details are provided in the requirements document attached with this brief. Also attaching other supporting documents with this brief mentioned in the document.
Updates
Font styles to use
Other font styles liked:
- Montserrat-Regular
Look and feel
Each slider illustrates characteristics of the customer's brand and the style your logo design should communicate.

```html
<!DOCTYPE html>
<html lang="en">
<head>
<meta charset="utf-8">
<title>Verdano Self Adhesive Vinyl Planks – 7 Plank Box</title>
<link rel="stylesheet" href="https://fonts.googleapis.com/css2?family=Montserrat:wght@400;500;600;700;800&display=swap">
<style>
  :root{
    --olive:#575243;
    --sage:#a7b5a7;
    --sage-edge:#95a395;
    --white:#ffffff;
    --ink:#2b2b2b;
    --page:#ffffff;
  }
  html,body{margin:0;padding:0;width:1200px;height:1000px;overflow:hidden;background:var(--page);}
  svg{display:block;font-family:"Montserrat",sans-serif;}
  .sage{fill:var(--sage);}
  .sage-edge{fill:var(--sage);stroke:var(--sage-edge);stroke-width:1;}
  .olive{fill:var(--olive);}
  .paper{fill:var(--white);}
  .brand{fill:var(--white);font-weight:500;letter-spacing:1px;}
  .brand-tag{fill:var(--white);font-size:7.5px;letter-spacing:2.6px;font-weight:500;}
  .headline{fill:var(--white);font-weight:700;}
  .sub{fill:var(--white);font-weight:400;}
  .caption{fill:var(--white);font-size:6px;text-anchor:middle;}
  .count-bar{fill:var(--olive);}
  .count{fill:var(--white);font-weight:700;}
  .spec{fill:var(--olive);font-weight:500;}
  .spec-box{fill:none;stroke:var(--olive);stroke-width:1.4;}
  .maker{fill:var(--olive);font-size:7px;text-anchor:end;}
  .maker-b{font-weight:700;}
  .doc-title{fill:var(--ink);font-size:6px;font-weight:700;}
  .step{fill:var(--ink);font-size:4px;font-weight:700;}
  .step-text{fill:#555;font-size:3.4px;}
  .thumb{fill:#cdb98c;}
  .table-line{stroke:var(--ink);stroke-width:.6;}
  .table-text{fill:var(--ink);font-size:4.6px;font-weight:600;}
  .swatch-text{fill:var(--white);font-size:14px;letter-spacing:.5px;}
</style>
</head>
<body>
<svg width="1200" height="1000" viewBox="0 0 1200 1000" xmlns="http://www.w3.org/2000/svg">

  <!-- dieline body -->
  <g class="dieline">
    <path class="sage-edge" d="M44 300 L44 285 L52 285 L52 300 Z M1150 300 L1150 285 L1158 285 L1158 300 Z"/>
    <rect class="sage-edge" x="52" y="285" width="1098" height="18"/>
    <rect class="sage-edge" x="44" y="300" width="1114" height="190"/>
    <rect class="sage-edge" x="52" y="490" width="1098" height="18"/>
    <rect class="sage-edge" x="40" y="505" width="1122" height="193"/>
    <rect class="sage-edge" x="57" y="698" width="1098" height="17"/>
  </g>

  <!-- ===== lid panel ===== -->
  <g class="lid-panel">
    <polygon class="olive" points="57,303 855,303 770,490 57,490"/>
    <polygon class="olive" points="868,303 886,303 801,490 783,490"/>
    <polygon class="olive" points="896,303 914,303 829,490 811,490"/>

    <g class="brand-lockup">
      <rect class="paper" x="82" y="322" width="22" height="22"/>
      <text class="brand" x="110" y="343" font-size="24">VERDANO</text>
      <text class="brand-tag" x="130" y="354">PREMIUM FLOORS AND TILES</text>
    </g>
    <text class="headline" x="82" y="425" font-size="24">SELF ADHESIVE</text>
    <text class="headline" x="82" y="450" font-size="24">VINYL PLANKS</text>
    <text class="sub" x="82" y="470" font-size="13">Suitable for general domestic use</text>

    <!-- installation instructions -->
    <g class="instructions">
      <rect class="paper" x="364" y="314" width="392" height="164" rx="5"/>
      <text class="doc-title" x="370" y="324">Installation instructions</text>

      <g class="column">
        <text class="step" x="370" y="331">Step 1 - Tools Needed</text>
        <rect class="thumb" x="370" y="334" width="22" height="20"/>
        <text class="step-text" x="396" y="338">Knife, ruler, pencil and a soft cloth.</text>
        <text class="step" x="370" y="363">Step 2 - Acclimatise your floor</text>
        <rect class="thumb" x="370" y="366" width="22" height="20" fill="#b9b9a6"/>
        <text class="step-text" x="396" y="370">Leave planks in the room for 24 hours.</text>
        <text class="step" x="370" y="415">Step 3 - Removing Skirting board</text>
        <rect class="thumb" x="370" y="418" width="22" height="20" fill="#6f6a5e"/>
        <text class="step-text" x="396" y="422">Carefully remove skirting boards first.</text>
        <text class="step" x="370" y="448">Step 4 - Planning your remove</text>
        <rect class="thumb" x="370" y="451" width="22" height="20"/>
        <text class="step-text" x="396" y="455">Mark a centre line across the room.</text>
      </g>
      <g class="column">
        <text class="step" x="500" y="331">Step 5 - Get ready to lay</text>
        <rect class="thumb" x="500" y="334" width="22" height="20" fill="#8d8677"/>
        <text class="step-text" x="526" y="338">Check the floor is clean and dry.</text>
        <text class="step" x="500" y="363">Step 6 - Dry lay your planks</text>
        <rect class="thumb" x="500" y="366" width="22" height="20" fill="#9fa69b"/>
        <text class="step-text" x="526" y="370">Lay out a row without the backing.</text>
        <text class="step" x="500" y="415">Step 7 - Arrows on the backing paper</text>
        <rect class="thumb" x="500" y="418" width="22" height="20" fill="#7e786b"/>
        <text class="step-text" x="526" y="422">Keep all arrows facing one way.</text>
        <text class="step" x="500" y="448">Step 8 - Laying the first plank</text>
        <rect class="thumb" x="500" y="451" width="22" height="20" fill="#6f6a5e"/>
        <text class="step-text" x="526" y="455">Peel the paper and press down firmly.</text>
      </g>
      <g class="column">
        <text class="step" x="630" y="331">Step 9 - Laying the remaining planks</text>
        <rect class="thumb" x="630" y="334" width="22" height="20" fill="#9fa69b"/>
        <text class="step-text" x="656" y="338">Butt each plank tight to the last.</text>
        <text class="step" x="630" y="363">Step 10 - Cutting the planks</text>
        <rect class="thumb" x="630" y="366" width="22" height="20" fill="#8d8677"/>
        <text class="step-text" x="656" y="370">Score the face with a sharp knife.</text>
        <text class="step" x="630" y="415">Step 11 - Breaking the cut plank</text>
        <rect class="thumb" x="630" y="418" width="22" height="20" fill="#7e786b"/>
        <text class="step-text" x="656" y="422">Bend the plank to snap the cut.</text>
        <text class="step" x="630" y="448">Step 12 - Laying the cut plank</text>
        <rect class="thumb" x="630" y="451" width="22" height="20" fill="#6f6a5e"/>
        <text class="step-text" x="656" y="455">Fit the cut edge against the wall.</text>
      </g>
    </g>

    <!-- maker details -->
    <g class="maker-details">
      <text class="maker maker-b" x="1001" y="326">Produced by :</text>
      <text class="maker" x="1001" y="334">Verdano</text>
      <text class="maker" x="1001" y="342">14 Mill Lane, Unit 3</text>
      <text class="maker" x="1001" y="350">Harrow, 40218</text>
      <text class="maker" x="1001" y="358">www.verdanofloors.com</text>
      <text class="maker maker-b" x="1001" y="366">Costumer Service :</text>
      <text class="maker" x="1001" y="374">555-014-2290</text>
    </g>

    <!-- conformity table -->
    <g class="conformity">
      <rect class="paper" x="894" y="385" width="106" height="88" stroke="#2b2b2b" stroke-width=".8"/>
      <rect x="926" y="390" width="42" height="26" fill="#2b2b2b"/>
      <line class="table-line" x1="894" y1="420" x2="1000" y2="420"/>
      <text class="table-text" x="947" y="426" text-anchor="middle">Verdano™</text>
      <text class="table-text" x="947" y="432" text-anchor="middle" font-weight="400">Premium Floors and Tiles</text>
      <line class="table-line" x1="894" y1="436" x2="1000" y2="436"/>
      <text class="table-text" x="896" y="442" font-size="4">EN 14041, EN 13501-1, EN 717-1, EN 13893</text>
      <line class="table-line" x1="894" y1="445" x2="1000" y2="445"/>
      <text class="table-text" x="896" y="451">Reaction to Fire</text><text class="table-text" x="997" y="451" text-anchor="end">Bfl-S1</text>
      <line class="table-line" x1="894" y1="454" x2="1000" y2="454"/>
      <text class="table-text" x="896" y="460">Emission of Formaldehyde</text><text class="table-text" x="997" y="460" text-anchor="end">E1</text>
      <line class="table-line" x1="894" y1="463" x2="1000" y2="463"/>
      <text class="table-text" x="896" y="470">Slipperiness</text><text class="table-text" x="997" y="470" text-anchor="end">DS</text>
    </g>

    <!-- pack info -->
    <g class="pack-info">
      <rect class="count-bar" x="1010" y="321" width="134" height="28"/>
      <text class="count" x="1070" y="346" font-size="22">7</text>
      <text class="count" x="1084" y="346" font-size="11">Planks</text>
      <text class="spec" x="1011" y="362" font-size="10.5" font-weight="700">Pack coverage 1 m²</text>
      <rect class="spec-box" x="1012" y="369" width="106" height="43"/>
      <text class="spec" x="1114" y="380" font-size="8" text-anchor="end">Plank Size :</text>
      <text class="spec" x="1114" y="390" font-size="8" text-anchor="end">914 mm x 152 mm</text>
      <text class="spec" x="1114" y="398" font-size="6" text-anchor="end">(36" x 6" approx.)</text>
      <text class="spec" x="1114" y="407" font-size="8" text-anchor="end">1.8 mm (0.07") Thickness</text>
    </g>
  </g>

  <!-- ===== front panel ===== -->
  <g class="front-panel">
    <rect x="752" y="508" width="203" height="190" role="img" aria-label="Photo of a bright bedroom with a bed, red throw and grey wood-effect plank floor" fill="url(#roomTone)"/>
    <defs>
      <linearGradient id="roomTone" x1="0" y1="0" x2="0" y2="1">
        <stop offset="0" stop-color="#e7eaee"/>
        <stop offset=".55" stop-color="#c9ccce"/>
        <stop offset="1" stop-color="#8e8d88"/>
      </linearGradient>
    </defs>
    <polygon class="olive" points="57,508 725,508 640,698 57,698"/>
    <polygon class="olive" points="738,508 756,508 671,698 653,698"/>
    <polygon class="olive" points="766,508 784,508 699,698 681,698"/>
    <polygon class="olive" points="747,510 827,698 667,698"/>
    <polygon class="paper" points="750,575 807,680 692,680"/>

    <g class="brand-lockup">
      <rect class="paper" x="82" y="526" width="22" height="22"/>
      <text class="brand" x="110" y="547" font-size="24">VERDANO</text>
      <text class="brand-tag" x="130" y="558">PREMIUM FLOORS AND TILES</text>
    </g>
    <text class="headline" x="82" y="653" font-size="31">SELF ADHESIVE VINYL PLANKS</text>
    <text class="sub" x="82" y="676" font-size="15">Suitable for general domestic use</text>

    <g class="feature-icons">
      <rect x="482" y="527" width="52" height="51" rx="5" fill="#d8d6c6" stroke="#fff" stroke-width="1.5" role="img" aria-label="Icon: plank being laid"/>
      <text class="caption" x="508" y="586">Easy to lay</text>
      <rect x="547" y="527" width="52" height="51" rx="5" fill="#e9a23b" stroke="#fff" stroke-width="1.5" role="img" aria-label="Icon: water and mop on floor"/>
      <text class="caption" x="573" y="586">Water resistant,</text>
      <text class="caption" x="573" y="592">easy to clean</text>
      <rect x="610" y="527" width="52" height="51" rx="5" fill="#9fd3df" stroke="#fff" stroke-width="1.5" role="img" aria-label="Icon: bathroom and kitchen"/>
      <text class="caption" x="636" y="586">Ideal for Bathrooms</text>
      <text class="caption" x="636" y="592">and Kitchens</text>
    </g>

    <g class="pack-info">
      <rect class="count-bar" x="960" y="527" width="184" height="30"/>
      <text class="count" x="1043" y="553" font-size="26">7</text>
      <text class="count" x="1060" y="553" font-size="14">Planks</text>
      <text class="spec" x="968" y="575" font-size="14" font-weight="600">Pack coverage 1 m²</text>
      <rect class="spec-box" x="960" y="583" width="158" height="55"/>
      <text class="spec" x="1114" y="598" font-size="12.5" font-weight="400" text-anchor="end">Plank Size :</text>
      <text class="spec" x="1114" y="611" font-size="12.5" font-weight="400" text-anchor="end">914 mm x 152 mm</text>
      <text class="spec" x="1114" y="621" font-size="9" font-weight="400" text-anchor="end">(36" x 6" approx.)</text>
      <text class="spec" x="1114" y="634" font-size="12.5" font-weight="400" text-anchor="end">1.8 mm (0.07") Thickness</text>
    </g>

    <g class="colour-swatch">
      <rect x="932" y="647" width="198" height="40" rx="4" fill="var(--olive)"/>
      <rect x="937" y="652" width="188" height="30" rx="2" fill="#8f8e88" role="img" aria-label="Wash grey wood grain swatch"/>
      <text class="swatch-text" x="940" y="674">WASH GREY</text>
    </g>
  </g>
</svg>
</body>
</html>
```